Business card design for sustainable building and development company

Need a business card design for a new sustainable building and real estate development company in the San Francisco Bay area. Name of company is "Tovrin Advisors, LLC" and we provide "Sustainable building, energy and development services" for residential and non residential projects. We'd like the following colors used but not all area required: green, gray, blue. Design should communicate innovation, professionalism and sustainability. Our current website is www.tovrin-advisors.example. Another possible design idea is to have the following listed on the back of the card:
Certified: VERN QS, Eco Marker Rater, DOLM Rater, Terravue Inspector, KSO TQ Building Analyst. Its not a must but could be text that could be used for back of card. Overall, we are open to a simple, clean design and or one with more text than usual for a card.

Industry/Entity Type

Real Estate

Contact Information for Business Card

Name on card: Mark J. Halvik
Title for Name: Principal + Founder
Phone: 555.814.0627
Email: mhalvik@tovrin-advisors.example
Website: www.tovrin-advisors.example

Also, please add the following for address:
San Francisco, California

Requirements
Nice to have
• If you can integrate the outline of a skyline on the backside of the card and if it looks good, I would like to see the design
Should not have
• a barcode;

```html
<!DOCTYPE html>
<html lang="en">
<head>
<meta charset="utf-8">
<title>Tovrin Advisors – Business Card</title>
<link href="https://fonts.googleapis.com/css2?family=Montserrat:wght@500;700&family=Open+Sans:wght@400;600&display=swap" rel="stylesheet">
<style>
  :root {
    --green: #6cbf3f;
    --green-deep: #4fae3a;
    --green-light: #7ccb4c;
    --ink: #1a1a1a;
    --gray: #8a8a8a;
    --gray-icon: #a6a6a6;
    --badge-fill: #d6dcd3;
    --paper: #ffffff;
    --backdrop: #c4c4c4;
  }
  * { margin: 0; padding: 0; box-sizing: border-box; }
  html, body { width: 1200px; height: 1000px; overflow: hidden; }
  body { background: var(--backdrop); position: relative; font-family: "Open Sans", sans-serif; }

  .card { position: absolute; overflow: hidden; }

  /* Front */
  .card-front { left: 42px; top: 24px; width: 780px; height: 456px; background: var(--paper); }
  .brand { position: absolute; left: 76px; top: 154px; display: flex; align-items: center; }
  .brand-dot { width: 160px; height: 160px; border-radius: 50%; background: var(--green); flex: none; }
  .brand-text { margin-left: 12px; }
  .brand-name {
    font-family: "Montserrat", sans-serif; font-weight: 700; font-size: 50px;
    color: var(--green); letter-spacing: -0.5px; line-height: 1; white-space: nowrap;
  }
  .brand-tagline {
    font-family: "Montserrat", sans-serif; font-weight: 500; font-size: 15.5px;
    color: var(--ink); text-transform: uppercase; margin-top: 8px; white-space: nowrap;
  }
  .front-band { position: absolute; left: 0; bottom: 0; width: 100%; height: 40px; background: var(--green); }
  .location-tab {
    position: absolute; left: 326px; bottom: 18px; width: 405px; height: 42px;
    background: var(--green); border-radius: 16px 16px 0 0;
    color: var(--paper); font-size: 26px; letter-spacing: 0.5px;
    display: flex; align-items: center; justify-content: center; padding-top: 6px;
  }

  /* Back */
  .card-back { left: 372px; top: 520px; width: 786px; height: 445px; background: var(--paper); }
  .back-field {
    position: absolute; left: 0; top: 0; width: 100%; height: 342px;
    background: linear-gradient(135deg, var(--green-light), var(--green) 55%, var(--green-deep));
  }
  .credentials { position: absolute; left: 14px; top: 17px; display: flex; flex-direction: column; gap: 13px; }
  .credential {
    width: 66px; height: 64px; background: var(--paper);
    display: flex; align-items: center; justify-content: center;
  }
  .credential span { display: block; width: 46px; height: 46px; background: var(--badge-fill); }

  .holder {
    position: absolute; right: 54px; top: 222px; text-align: right; color: var(--paper);
  }
  .holder-name { font-weight: 600; font-size: 56px; line-height: 1.1; letter-spacing: 0.3px; white-space: nowrap; }
  .holder-title { font-weight: 400; font-size: 20px; letter-spacing: 0.6px; margin-top: 0; white-space: nowrap; }

  .contact-tab {
    position: absolute; left: 328px; top: 323px; width: 407px; height: 40px;
    background: var(--paper); border-radius: 16px 16px 0 0;
  }
  .contact-list { position: absolute; left: 352px; top: 336px; list-style: none; }
  .contact-item { display: flex; align-items: center; height: 36px; color: var(--gray); font-size: 21px; letter-spacing: 0.4px; white-space: nowrap; }
  .contact-icon {
    width: 25px; height: 25px; border-radius: 5px; background: var(--gray-icon);
    margin-right: 9px; flex: none; display: flex; align-items: center; justify-content: center;
  }
  .contact-icon svg { width: 17px; height: 17px; }
</style>
</head>
<body>

  <section class="card card-front" aria-label="Card front">
    <div class="brand">
      <div class="brand-dot" aria-hidden="true"></div>
      <div class="brand-text">
        <div class="brand-name">Tovrin Advisors</div>
        <div class="brand-tagline">Sustainable Building, Energy &amp; Development Services</div>
      </div>
    </div>
    <div class="front-band"></div>
    <div class="location-tab">San Francisco, California</div>
  </section>

  <section class="card card-back" aria-label="Card back">
    <div class="back-field"></div>

    <div class="credentials">
      <div class="credential" role="img" aria-label="VERN QS certification badge"><span></span></div>
      <div class="credential" role="img" aria-label="Terravue inspector badge"><span></span></div>
      <div class="credential" role="img" aria-label="KSO TQ building analyst badge"><span></span></div>
      <div class="credential" role="img" aria-label="Eco Marker rater badge"><span></span></div>
    </div>

    <div class="holder">
      <div class="holder-name">Mark J. Halvik</div>
      <div class="holder-title">Principal + Founder</div>
    </div>

    <div class="contact-tab"></div>
    <ul class="contact-list">
      <li class="contact-item">
        <span class="contact-icon">
          <svg viewBox="0 0 24 24" aria-hidden="true"><path fill="#fff" d="M6.6 10.8a15 15 0 0 0 6.6 6.6l2.2-2.2a1 1 0 0 1 1-.25 11.4 11.4 0 0 0 3.6.57 1 1 0 0 1 1 1V20a1 1 0 0 1-1 1A17 17 0 0 1 3 4a1 1 0 0 1 1-1h3.5a1 1 0 0 1 1 1c0 1.25.2 2.45.57 3.6a1 1 0 0 1-.25 1z"/></svg>
        </span>555.814.0627
      </li>
      <li class="contact-item">
        <span class="contact-icon">
          <svg viewBox="0 0 24 24" aria-hidden="true"><circle cx="12" cy="12" r="4" fill="none" stroke="#fff" stroke-width="2.2"/><path d="M16 9v4.5a2.5 2.5 0 0 0 5 0V12a9 9 0 1 0-3.5 7.1" fill="none" stroke="#fff" stroke-width="2.2"/></svg>
        </span>mhalvik@tovrin-advisors.example
      </li>
      <li class="contact-item">
        <span class="contact-icon">
          <svg viewBox="0 0 24 24" aria-hidden="true"><circle cx="12" cy="12" r="9" fill="none" stroke="#fff" stroke-width="2"/><path d="M3 12h18M12 3c3 3 3 15 0 18M12 3c-3 3-3 15 0 18" fill="none" stroke="#fff" stroke-width="1.6"/></svg>
        </span>www.tovrin-advisors.example
      </li>
    </ul>
  </section>

</body>
</html>
```